Wordpress Design Project for Bankruptcy Law Office in San Francisco

our current website: www.dorvanelilaw-example.com

we would like to re-design it for wordpress to make it faster and a bit more modern.

content should be similar to what we have there right now but also we do family law

please include logo for law office:

Law Office of Marta K. Dolvenidze

Thank you.
Updates

please see attached word document with logos that we like as an example.

we do tend to like color red.  darker red.

Please submit your design variations and logo as soon as possible.   We would like to go over them and make our decision

Reason: Please create couple of more variations of logo for your design, so we can make our decision what we like the most. Please see word doc for samples: Text: Law Office Of Marta K. Dolvenidze

Reason: final touches

Target Market(s)

bankruptcy and family law clients

Industry/Entity Type

Family Law

Requirements
Must have
• see examples of law sites
http://promo.lexorbin-example.com/testimonials

- new logo: Law Office of Marta K. Dolvenidze
- client intake form
- blog
- contact us form

Nice to have
• - map
- red color
- on the front page a nice photo of SF or a happy family

```html
<!DOCTYPE html>
<html lang="en">
<head>
<meta charset="utf-8">
<title>Ledgerline Law — Law Office of Marta K. Dolvenidze</title>
<link href="https://fonts.googleapis.com/css2?family=Hind:wght@400;500;600;700&family=Arimo:wght@700&display=swap" rel="stylesheet">
<style>
:root{
  --teal-dark:#1d5470;
  --teal:#2b7394;
  --teal-nav:#2f7a9b;
  --teal-side:#2a6784;
  --sky:#c9ddec;
  --sky-light:#e4eef6;
  --text:#3a3a3a;
  --link:#2a6c8d;
  --band:#f5f5f5;
  --footer:#ececec;
  --white:#fff;
}
*{box-sizing:border-box;margin:0;padding:0}
html,body{width:712px;height:1200px;overflow:hidden;background:var(--white)}
body{position:relative;font-family:"Hind",sans-serif;color:var(--text);font-size:7.4px;line-height:1.6}
.abs{position:absolute}

.top-rule{left:0;top:0;width:712px;height:3px;background:var(--teal-dark)}
.header{left:0;top:3px;width:712px;height:85px;background:var(--white)}
.brand{left:18px;top:24px;display:flex;align-items:center;gap:6px}
.brand-mark{width:14px;height:14px;background:var(--teal)}
.brand-name{font-family:"Hind",sans-serif;font-weight:700;font-size:27px;line-height:1;color:var(--teal)}
.brand-office{left:19px;top:71px;font-size:8.5px;color:var(--teal)}
.lang{right:22px;top:17px;display:flex;align-items:center;gap:6px;font-size:8px;color:var(--teal)}
.lang-select{width:77px;height:17px;background:#e3ebf1;color:#3a3a3a;font-size:7.5px;padding:2px 5px;display:flex;justify-content:space-between;align-items:center}
.call{right:20px;top:52px;font-size:11px;color:var(--teal);letter-spacing:.2px}
.call strong{font-weight:500;font-size:16px;color:#111;margin-left:4px}

.nav{left:0;top:88px;width:712px;height:31px;background:linear-gradient(#3585a7,#256c8d);display:flex}
.nav a{color:var(--white);text-decoration:none;font-size:10px;line-height:31px;padding:0 16px;border-right:1px solid rgba(255,255,255,.25);white-space:nowrap}
.nav a:first-child{padding:0 17px 0 30px}

.hero{left:0;top:119px;width:712px;height:246px;background:linear-gradient(90deg,#d9c3a8 0%,#c8b9a8 40%,#c5d9e9 62%,var(--sky) 100%)}
.hero-copy{left:426px;top:192px;width:270px;font-family:"Arimo",sans-serif;font-weight:700;color:#3e86a8;font-size:14.5px;line-height:1.55}
.hero-copy .lead{font-size:27px;color:var(--teal-dark);margin-right:6px}

.services{left:0;top:365px;width:712px;height:175px;background:var(--band)}
.service{position:absolute;top:14px;width:162px}
.service h3{font-size:10.5px;font-weight:500;color:#111;margin-bottom:3px}
.service .thumb{width:160px;height:66px;border:2px solid var(--white);box-shadow:0 0 2px rgba(0,0,0,.3);margin-bottom:7px}
.service h4{font-size:9px;font-weight:600;color:var(--teal-dark);line-height:1.3}
.service p{font-size:7.3px;color:var(--link);line-height:1.6}

.main{left:12px;top:553px;width:480px}
.main h2{font-size:10.5px;font-weight:500;color:#111;margin-bottom:5px}
.main p{margin-bottom:4px}
.main h5{font-size:7.4px;font-weight:700;margin:3px 0 2px}
.divider{border-top:1px dotted #999;margin:12px 0 14px}
.story{display:flex;gap:10px;margin:8px 0 4px}
.story .thumb{flex:none;width:152px;height:101px}
.story h6{font-size:9px;font-weight:600;color:var(--teal-dark);margin-bottom:3px}

.sidebar{left:505px;top:540px;width:207px;height:610px;background:var(--teal-side)}
.side-head{height:30px;background:var(--teal-dark);border-bottom:2px solid #4f8eab;color:var(--white);font-size:12px;padding:7px 12px;font-variant:small-caps;letter-spacing:.3px}
.form{padding:3px 13px 10px}
.form label{display:block;color:var(--white);font-size:8px;line-height:1;margin:5px 0 4px}
.form .field{height:17px;background:var(--white)}
.form .area{height:46px;background:var(--white)}
.check{display:flex;align-items:center;gap:6px;color:var(--white);font-size:7.4px;margin:7px 0 11px}
.check span.box{width:8px;height:8px;background:#e8e8e8}
.buttons{display:flex;gap:12px}
.btn{background:#0f3a52;color:var(--white);font-size:8px;font-weight:600;padding:3px 10px;border-radius:2px}
.news{padding:10px 14px}
.news-item{margin-bottom:11px}
.news-item h6{font-size:9px;font-weight:400;color:var(--white);line-height:1.3;margin-bottom:1px}
.news-item p{font-style:italic;color:var(--white);font-size:7.3px;line-height:1.55}
.news-item b{display:block;color:var(--white);font-size:7.6px;margin-top:3px}

.footer{left:0;top:1150px;width:712px;height:50px;background:var(--footer);font-size:7.4px;color:#222}
.footer .copy{position:absolute;left:14px;top:12px}
.footer .links{position:absolute;right:21px;top:12px;word-spacing:1px}
</style>
</head>
<body>
<div class="abs top-rule"></div>
<header class="abs header"></header>
<div class="abs brand"><span class="brand-mark"></span><span class="brand-name">Ledgerline Law</span></div>
<div class="abs brand-office">Law Office of Marta K. Dolvenidze</div>
<div class="abs lang">Select Language <span class="lang-select">English
  <svg width="6" height="4" viewBox="0 0 6 4"><path d="M0 0h6L3 4z" fill="#333"/></svg></span></div>
<div class="abs call">CALL US NOW: <strong>(555) 014-2290</strong></div>

<nav class="abs nav">
  <a>HOME</a><a>ABOUT US</a><a>AREAS OF PRACTISE</a><a>RESOURCES</a><a>BLOG</a><a>FAQ</a><a style="border:0">CONTACT US</a>
</nav>

<div class="abs hero" role="img" aria-label="Smiling family of four against a pale blue sky"></div>
<div class="abs hero-copy"><span class="lead">Lorem Ipsum</span>is simply dummy text of the printing and typesetting industry.</div>

<section class="abs services">
  <div class="service" style="left:15px">
    <h3>Debt Relief</h3>
    <div class="thumb" role="img" aria-label="Relieved man in a field with papers flying" style="background:linear-gradient(#7f9a5a,#5e7a3c)"></div>
    <h4>Tittle goes here</h4>
    <p>Lorem ipsum dolor sit amet, consectetur adipisicing elit, sed do eiusmod tempor incididunt ut labore et dolore magna</p>
  </div>
  <div class="service" style="left:191px">
    <h3>Fore Closure Prevention</h3>
    <div class="thumb" role="img" aria-label="For sale sign on a white picket fence" style="background:linear-gradient(90deg,#5a5a5a,#c9302f 45%,#b52626 70%,#d8d8d8)"></div>
    <h4>Tittle goes here</h4>
    <p>Lorem ipsum dolor sit amet, consectetur adipisicing elit, sed do eiusmod tempor incididunt ut labore et dolore magna</p>
  </div>
  <div class="service" style="left:368px">
    <h3>Chapter 13</h3>
    <div class="thumb" role="img" aria-label="Open law book on a wooden desk" style="background:linear-gradient(#4a2f1e,#a27a55 60%,#6b4127)"></div>
    <h4>Tittle goes here</h4>
    <p>Lorem ipsum dolor sit amet, consectetur adipisicing elit, sed do eiusmod tempor incididunt ut labore et dolore magna</p>
  </div>
  <div class="service" style="left:545px">
    <h3>Chapter 7</h3>
    <div class="thumb" role="img" aria-label="Row of leather-bound law books" style="background:linear-gradient(90deg,#2a211b,#8a5531 40%,#3b2a1f 70%,#8a5531)"></div>
    <h4>Tittle goes here</h4>
    <p>Lorem ipsum dolor sit amet, consectetur adipisicing elit, sed do eiusmod tempor incididunt ut labore et dolore magna</p>
  </div>
</section>

<main class="abs main">
  <h2>WELCOME TO LEDGERLINE LAW - COMPLETE BANKRUPTCY INFORMATION</h2>
  <p>The Law Offices of Marta K. Dolvenidze is a consumer law office dedicated to consumer protection and zealously defending the rights of our clients. We offer the big firm quality legal representation with a small firm individualized attention to each client.</p>
  <p>Our office offers services in: all types of consumer bankruptcy filings, i.e. Chapter 7, Chapter 13, Chapter 11, negotiating a settlement of your debts, assisting you in the defense of collection litigation and defending you against foreclosure. Please review our site and see what we may be able to offer you. Feel free to call us at (555) 013-0482 or use our free case evaluation form.</p>
  <h5>Speak to a Lawyer</h5>
  <p>Unlike some other law firms, when you call the Law Office of Marta K. Dolvenidze you will speak to an actual attorney. Not a paralegal or assistant. And even after retaining our office you will still speak to an attorney unlike other firms where you cannot get a hold of your attorney after several attempts.</p>
  <p style="margin-top:8px">Lorem ipsum dolor sit amet, consectetuer adipiscing elit. Nam cursus. Morbi ut mi. Nullam enim leo, egestas id, condimentum at, laoreet mattis, massa. Sed eleifend nonummy diam. Praesent mauris ante, elementum et, bibendum at, posuere sit amet, nibh. Duis tincidunt lectus quis dui viverra vestibulum. Suspendisse vulputate aliquam dui. Nulla elementum dui ut augue. Aliquam vehicula mi at mauris. Maecenas placerat, nisl at consequat rhoncus, sem nunc gravida justo, quis eleifend arcu velit quis lacus. Morbi magna magna, tincidunt a, mattis non, imperdiet vitae</p>
  <div class="divider"></div>
  <h2>STORIES &amp; MORE INFORMATION</h2>
  <div class="story">
    <div class="thumb" role="img" aria-label="Judge's gavel resting on a book" style="background:linear-gradient(135deg,#2b1a12,#8a4a25 55%,#3a2016)"></div>
    <div>
      <h6>Story Tittle line goes here</h6>
      <p>Lorem ipsum dolor sit amet, consectetuer adipiscing elit. Nam cursus. Morbi ut mi. Nullam enim leo, egestas id, condimentum at, laoreet mattis, massa.</p>
      <p>Sed eleifend nonummy diam. Praesent mauris ante, elementum et, bibendum at, posuere sit amet, nibh. Duis tincidunt lectus quis dui viverra vestibulum. Suspendisse vulputate aliquam dui. Nulla elementum dui ut augue. Aliquam vehicula mi at mauris. Maecenas placerat, nisl at consequat rhoncus, sem nunc gravida justo, quis eleifend arcu velit quis lacus. Morbi magna magna, tincidunt a, mattis non, imperdiet vitae, tellus.</p>
    </div>
  </div>
  <p>Mauris vel lacus vitae felis vestibulum volutpat. Etiam est nunc, venenatis in, tristique eu, imperdiet ac, nisl. Cum sociis natoque penatibus et magnis dis parturient montes, nascetur ridiculus mus. In iaculis facilisis massa.</p>
  <div class="story" style="margin-top:18px">
    <div class="thumb" role="img" aria-label="Family with children on bicycles in a park" style="background:linear-gradient(#a9c27a,#7c9a4e 60%,#b7474a)"></div>
    <div>
      <h6>Story Tittle line goes here</h6>
      <p>Lorem ipsum dolor sit amet, consectetuer adipiscing elit. Nam cursus. Morbi ut mi. Nullam enim leo, egestas id, condimentum at, laoreet mattis, massa.</p>
      <p>Sed eleifend nonummy diam. Praesent mauris ante, elementum et, bibendum at, posuere sit amet, nibh. Duis tincidunt lectus quis dui viverra vestibulum. Suspendisse vulputate aliquam dui. Nulla elementum dui ut augue. Aliquam vehicula mi at mauris. Maecenas placerat, nisl at consequat rhoncus, sem nunc gravida justo, quis eleifend arcu velit quis lacus. Morbi magna magna, tincidunt a, mattis non, imperdiet vitae, tellus.</p>
    </div>
  </div>
  <p>Mauris vel lacus vitae felis vestibulum volutpat. Etiam est nunc, venenatis in, tristique eu, imperdiet ac, nisl. Cum sociis natoque penatibus et magnis dis parturient montes, nascetur ridiculus mus. In iaculis facilisis massa.</p>
</main>

<aside class="abs sidebar">
  <div class="side-head">Contact Form</div>
  <div class="form">
    <label>Name:</label><div class="field"></div>
    <label>Email:</label><div class="field"></div>
    <label>Phone:</label><div class="field"></div>
    <label>Subject:</label><div class="field"></div>
    <label>Message:</label><div class="area"></div>
    <div class="check"><span class="box"></span>Send a copy of this message to yourself</div>
    <div class="buttons"><span class="btn">SEND</span><span class="btn">RESET</span></div>
  </div>
  <div class="side-head" style="margin-top:3px">Recent Blog &amp; News</div>
  <div class="news">
    <div class="news-item"><h6>Tittle line here</h6><p>Lorem ipsum dolor sit amet, consectetuer adipiscing elit. Nam cursus. Morbi ut mi. Nullam enim leo, egestas id, condimentum at, laoreet mattis, massa.</p><b>LEARN MORE</b></div>
    <div class="news-item"><h6>Tittle line here</h6><p>Lorem ipsum dolor sit amet, consectetuer adipiscing elit. Nam cursus. Morbi ut mi. Nullam enim leo, egestas id, condimentum at, laoreet mattis, massa.</p><b>LEARN MORE</b></div>
    <div class="news-item"><h6>Tittle line here</h6><p>Proin dui lectus, cursus eu, mattis laoreet, viverra sit amet, quam. Curabitur vel dolor ultrices ipsum dictum tristique. Praesent vitae lacus. Ut velit enim, vestibulum non, fermentum nec, hendrerit quis, leo. Pellentesque rutrum malesuada neque.</p><b>LEARN MORE</b></div>
  </div>
</aside>

<footer class="abs footer">
  <span class="copy">© 2012 Company Name &nbsp;|&nbsp; All right reserved &nbsp;|&nbsp; Term &amp; Conditions</span>
  <span class="links">HOME &nbsp;|&nbsp; ABOUT US &nbsp;|&nbsp; AREAS OF PRACTISE &nbsp;|&nbsp; RESOURCES &nbsp;|&nbsp; BLOG &nbsp;|&nbsp; FAQ &nbsp;|&nbsp; CONTACT US</span>
</footer>
</body>
</html>
```